VENTURE CAPITAL GROUP BUSINESS CARD DESIGN

Venture Capital Group based in SF looking for a bold business card design. No trendy colour explosion, 3D effects etc. Just "simple" optical effects. Works on your brain, keeps your eye focused and sticks to your mind.
Target Market(s)
Technology startups
Industry/Entity Type
Venture Capital
Contact Information for Business Card
DESMOND WHITLAKE
MANAGING PARTNER
187 FENWORTH ST SAN FRANCISCO, CA 94187
415.555.0142 O
415.555.0147 F
415.555.0193 C
desmond@veldtmoorcapital.ventures

```html
<!DOCTYPE html>
<html lang="en">
<head>
<meta charset="utf-8">
<title>Veldtmoor Capital Group – Business Card</title>
<link rel="stylesheet" href="https://fonts.googleapis.com/css2?family=Open+Sans:ital,wght@0,400;0,600;0,700;1,400&display=swap">
<style>
  :root {
    --backdrop: #8e8f8f;
    --card-white: #eceef0;
    --brand-green: #1d6b23;
    --brand-green-dark: #0d4412;
    --brand-green-glow: #3f9e3f;
    --ink: #4a4d50;
    --ink-soft: #7b7e82;
    --mark-grey: #d9dbdd;
    --white: #ffffff;
  }
  * { margin: 0; padding: 0; box-sizing: border-box; }
  html, body {
    width: 1105px; height: 1200px; overflow: hidden;
    background: var(--backdrop);
    font-family: "Open Sans", Arial, sans-serif;
  }
  .card {
    position: absolute;
    left: 172px;
    width: 760px;
    height: 434px;
    box-shadow: 0 14px 22px rgba(0,0,0,0.35);
  }
  .card--front { top: 140px; background: var(--card-white); }
  .card--back {
    top: 674px;
    background: radial-gradient(ellipse at 50% 42%, var(--brand-green-glow) 0%, #227a27 40%, var(--brand-green-dark) 100%);
  }

  /* front */
  .brand-mark {
    position: absolute; left: 107px; top: 31px;
    width: 104px; height: 104px; border-radius: 50%;
    background: radial-gradient(circle at 40% 35%, #f4f5f6, var(--mark-grey));
  }
  .brand-name {
    position: absolute; left: 37px; top: 160px;
    font-size: 33px; font-weight: 600; color: var(--brand-green);
    letter-spacing: 0.5px; line-height: 1;
  }
  .address {
    position: absolute; left: 37px; top: 234px;
    font-size: 19px; line-height: 25px; color: var(--ink);
  }
  .contact-list {
    position: absolute; left: 37px; top: 288px;
    list-style: none; font-size: 19px; color: var(--ink);
  }
  .contact-list li { display: flex; align-items: center; height: 29.5px; }
  .contact-list svg { width: 18px; height: 18px; margin-right: 11px; fill: var(--brand-green-dark); flex: none; }
  .person {
    position: absolute; right: 52px; top: 285px; text-align: right;
  }
  .person-name { font-size: 25px; font-weight: 700; color: var(--brand-green-dark); line-height: 32px; }
  .person-title { font-size: 20px; color: var(--ink-soft); line-height: 28px; }

  /* back */
  .back-mark {
    position: absolute; left: 310px; top: 92px;
    width: 140px; height: 140px; border-radius: 50%;
    background: radial-gradient(circle at 40% 35%, #f2f3f4, #c9cccf);
  }
  .back-name {
    position: absolute; left: 0; right: 0; top: 254px; text-align: center;
    font-size: 26px; font-weight: 600; color: var(--white); letter-spacing: 0.5px;
  }
  .website {
    position: absolute; left: 0; right: 0; top: 356px; text-align: center;
    font-size: 21px; font-style: italic; color: var(--white); letter-spacing: 1.6px;
  }
</style>
</head>
<body>
  <section class="card card--front">
    <div class="brand-mark"></div>
    <div class="brand-name">Veldtmoor Capital Group</div>
    <div class="address">187 Fenworth ST<br>San Francisco, CA 94187</div>
    <ul class="contact-list">
      <li>
        <svg viewBox="0 0 24 24" aria-hidden="true"><path d="M6.6 10.8a15.1 15.1 0 0 0 6.6 6.6l2.2-2.2a1 1 0 0 1 1-.25 11.4 11.4 0 0 0 3.6.57 1 1 0 0 1 1 1V20a1 1 0 0 1-1 1A17 17 0 0 1 3 4a1 1 0 0 1 1-1h3.5a1 1 0 0 1 1 1c0 1.25.2 2.45.57 3.57a1 1 0 0 1-.25 1z"/></svg>
        415.555.0142
      </li>
      <li>
        <svg viewBox="0 0 24 24" aria-hidden="true"><path d="M7 1h10a2 2 0 0 1 2 2v18a2 2 0 0 1-2 2H7a2 2 0 0 1-2-2V3a2 2 0 0 1 2-2zm0 3v14h10V4zm5 15.2a1.2 1.2 0 1 0 0 2.4 1.2 1.2 0 0 0 0-2.4z"/></svg>
        415.555.0193
      </li>
      <li>
        <svg viewBox="0 0 24 24" aria-hidden="true"><path d="M6 2h12v5H6zM4 8h16a2 2 0 0 1 2 2v7h-4v5H6v-5H2v-7a2 2 0 0 1 2-2zm4 8v4h8v-4z"/></svg>
        415.555.0147
      </li>
      <li>
        <svg viewBox="0 0 24 24" aria-hidden="true"><path d="M2 5h20v14H2zm2 2v.5l8 5 8-5V7zm0 2.9V17h16V9.9l-8 5z"/></svg>
        desmond@veldtmoorcapital.ventures
      </li>
    </ul>
    <div class="person">
      <div class="person-name">Desmond Whitlake</div>
      <div class="person-title">Managing Partner</div>
    </div>
  </section>

  <section class="card card--back">
    <div class="back-mark"></div>
    <div class="back-name">Veldtmoor Capital Group</div>
    <div class="website">www.veldtmoorcapital.ventures</div>
  </section>
</body>
</html>
```